Real Estate Company / Capital Needs Cards!

need business cards designed using the logos that were just designed by pixelbarn.

Reason: per designers request deadline extended 1 day…thank you.

Target Market(s)

Investors and clients looking to purchase real estate or invest in the business.

Industry/Entity Type

Business

Requirements
Must have
• two designs - one for the real estate logo and one for the capital logo, similar but slightly different.
Nice to have
• something to make it pop (perhaps on the back)
Should not have
• much color

```html
<!DOCTYPE html>
<html lang="en">
<head>
<meta charset="utf-8">
<title>Veldmar Real Estate – Business Cards</title>
<link href="https://fonts.googleapis.com/css2?family=Cinzel:wght@400;600&display=swap" rel="stylesheet">
<style>
  :root {
    --page: #e9e6e2;
    --card: #0a0a0a;
    --ink: #e2e2e2;
    --ink-soft: #cfcfcf;
    --mark-faint: #1c1c1c;
  }
  * { margin: 0; padding: 0; box-sizing: border-box; }
  html, body { width: 1200px; height: 498px; overflow: hidden; }
  body {
    background: var(--page);
    font-family: "Cinzel", serif;
    color: var(--ink);
  }
  .sheet {
    width: 1200px; height: 498px;
    display: flex; align-items: center; justify-content: center; gap: 60px;
  }
  .card {
    position: relative;
    width: 520px; height: 300px;
    background: var(--card);
    border-radius: 26px;
    overflow: hidden;
  }
  /* Front */
  .brand {
    position: absolute; top: 40px; left: 34px;
    display: flex; align-items: center; gap: 12px;
  }
  .brand-square {
    width: 50px; height: 50px; background: var(--ink); border-radius: 4px;
  }
  .brand-name {
    font-weight: 400; line-height: 1; color: var(--ink);
  }
  .brand-name .line1 { display: block; font-size: 34px; letter-spacing: 1px; }
  .brand-name .line2 { display: block; font-size: 14px; letter-spacing: 2px; margin-top: 4px; }
  .contact {
    position: absolute; left: 40px; top: 160px;
    font-size: 14px; line-height: 1.45; color: var(--ink-soft);
  }
  .contact .person { font-size: 19px; color: var(--ink); margin-bottom: 4px; }
  .contact .address { margin-top: 10px; font-size: 15px; }
  /* Back */
  .back-square {
    position: absolute; left: 170px; top: 50px;
    width: 180px; height: 200px;
    background: var(--mark-faint); border-radius: 18px;
  }
  .back-name {
    position: absolute; inset: 0;
    display: flex; flex-direction: column; align-items: center; justify-content: center;
    font-weight: 400; color: var(--ink); text-align: center;
  }
  .back-name .line1 { font-size: 68px; letter-spacing: 3px; line-height: 1; }
  .back-name .line2 { font-size: 30px; letter-spacing: 6px; margin-top: 6px; }
</style>
</head>
<body>
  <main class="sheet">
    <section class="card card-front">
      <div class="brand">
        <span class="brand-square"></span>
        <span class="brand-name">
          <span class="line1">VELDMAR</span>
          <span class="line2">REAL ESTATE</span>
        </span>
      </div>
      <div class="contact">
        <p class="person">Your Name, Title</p>
        <p>P: 555-014-2739</p>
        <p>F: 555-018-6642</p>
        <p>E: veldmarrealestate@mailbox.com</p>
        <p class="address">Street Name City Name State ZipCode</p>
      </div>
    </section>
    <section class="card card-back">
      <span class="back-square"></span>
      <div class="back-name">
        <span class="line1">VELDMAR</span>
        <span class="line2">REAL ESTATE</span>
      </div>
    </section>
  </main>
</body>
</html>
```